I have a logo and need to design the business card and stationery.
Updates

The uploaded logo image named as GREYMARSH CONSTRUCTION which is to be replaced to GREYMARSH CONTRACTS. Kindly add below details and submit the designs- Company name- Greymarsh Engineering Contracts LLP Name & Post- Kelvan Joshi (Designated Partner) Address- Block No.317, Wing C, Tulvo Trade Court, Manek Pural Road, Ruparel Industrial Estate, Goregaon(E), Mumbai - 400 063 Contact- +91 97415 60382 Email- kelvanjoshi@mailbrook.example Website- www.greymarshcontracts.example Contact for Letterhead- +91-22-28754193

Hi Tovin Rahul, We are liking your Design #28860835. We have suggested some changes which are mentioned in feedback. Kindly revert with it asap to finalize this design.

Colors

Designer to choose colors to be used in the design.

```html
<!DOCTYPE html>
<html lang="en">
<head>
<meta charset="utf-8">
<title>Greymarsh Contracts – Business Card</title>
<link href="https://fonts.googleapis.com/css2?family=Poppins:wght@400;600&family=Open+Sans:wght@400&display=swap" rel="stylesheet">
<style>
  :root {
    --canvas-bg: #b9b9b9;
    --card-dark-top: #2a2a2a;
    --card-dark-bottom: #0b0b0b;
    --card-light: #ffffff;
    --ink: #2b2b2b;
    --ink-soft: #3c3c3c;
    --mark-light: #d4d4d4;
  }
  * { box-sizing: border-box; margin: 0; padding: 0; }
  html, body { width: 1200px; height: 1200px; overflow: hidden; }
  body {
    position: relative;
    background: var(--canvas-bg);
    font-family: "Poppins", sans-serif;
    color: var(--ink);
  }
  .card {
    position: absolute;
    top: 303px;
    height: 594px;
  }
  .card-front {
    left: 200px;
    width: 370px;
  }
  .front-surface {
    position: absolute;
    inset: 0;
    background: linear-gradient(170deg, var(--card-dark-top) 0%, #1c1c1c 45%, var(--card-dark-bottom) 100%);
  }
  .front-square {
    position: absolute;
    left: 290px;
    top: 395px;
    width: 34px;
    height: 34px;
    border: 4px solid var(--mark-light);
  }
  .front-name {
    position: absolute;
    left: 38px;
    right: 38px;
    top: 482px;
    font-weight: 600;
    color: var(--mark-light);
    text-align: center;
    line-height: 1.1;
  }
  .front-name .line-1 { display: block; font-size: 29px; letter-spacing: 0.5px; }
  .front-name .line-2 { display: block; font-size: 20px; letter-spacing: 9px; margin-right: -9px; }

  .card-back {
    left: 599px;
    width: 364px;
    background: var(--card-light);
    text-align: center;
  }
  .back-brand {
    position: absolute;
    top: 372px;
    left: 0; right: 0;
  }
  .back-brand {
    top: 45px;
    display: flex;
    flex-direction: column;
    align-items: center;
    gap: 14px;
  }
  .brand-square {
    width: 92px;
    height: 92px;
    border: 9px solid var(--ink);
  }
  .brand-name {
    font-weight: 600;
    font-size: 17px;
    letter-spacing: 2px;
    color: var(--ink);
  }
  .person-name {
    position: absolute;
    top: 228px; left: 0; right: 0;
    font-weight: 600;
    font-size: 21px;
    color: var(--ink);
  }
  .person-role {
    position: absolute;
    top: 257px; left: 0; right: 0;
    font-family: "Open Sans", sans-serif;
    font-size: 15px;
    color: var(--ink-soft);
  }
  .contact-icons {
    position: absolute;
    top: 299px; left: 0; right: 0;
    display: flex;
    justify-content: center;
    gap: 10px;
  }
  .contact-icon {
    width: 30px; height: 30px;
    border: 2px solid var(--ink);
    border-radius: 5px;
    display: flex; align-items: center; justify-content: center;
  }
  .contact-list {
    position: absolute;
    top: 341px; left: 0; right: 0;
    list-style: none;
    font-size: 17px;
    line-height: 22.5px;
    color: var(--ink-soft);
  }
  .company {
    position: absolute;
    top: 436px; left: 0; right: 0;
    font-weight: 600;
    color: var(--ink);
  }
  .company .line-1 { display: block; font-size: 18.5px; line-height: 24px; }
  .company .line-2 { display: block; font-size: 17px; letter-spacing: 8.6px; margin-right: -8.6px; line-height: 22px; }
  .address {
    position: absolute;
    top: 489px; left: 0; right: 0;
    font-style: normal;
    font-size: 13.6px;
    line-height: 19.5px;
    color: var(--ink-soft);
  }
</style>
</head>
<body>

<section class="card card-front">
  <div class="front-surface" role="img" aria-label="Dark background with a repeating decorative geometric pattern"></div>
  <div class="front-square"></div>
  <p class="front-name"><span class="line-1">GREYMARSH</span><span class="line-2">CONTRACTS</span></p>
</section>

<section class="card card-back">
  <div class="back-brand">
    <div class="brand-square"></div>
    <p class="brand-name">GREYMARSH CONTRACTS</p>
  </div>

  <h1 class="person-name">KELVAN JOSHI</h1>
  <p class="person-role">Designated Partner</p>

  <div class="contact-icons">
    <span class="contact-icon">
      <svg width="18" height="18" viewBox="0 0 24 24" aria-label="Phone"><path d="M6.6 2.5l3 3.2-1.9 2.4c1.2 2.7 3.5 5 6.2 6.2l2.4-1.9 3.2 3-2 3.3C11 18 5.8 12.8 4 5.3z" fill="none" stroke="#2b2b2b" stroke-width="1.8" stroke-linejoin="round"/></svg>
    </span>
    <span class="contact-icon">
      <svg width="18" height="18" viewBox="0 0 24 24" aria-label="Email"><rect x="2.5" y="5" width="19" height="14" fill="#2b2b2b"/><path d="M3 6l9 7 9-7" fill="none" stroke="#fff" stroke-width="1.6"/></svg>
    </span>
    <span class="contact-icon">
      <svg width="18" height="18" viewBox="0 0 24 24" aria-label="Website"><g fill="none" stroke="#2b2b2b" stroke-width="1.5"><circle cx="12" cy="12" r="9"/><ellipse cx="12" cy="12" rx="4" ry="9"/><path d="M3 12h18M4.5 7.5h15M4.5 16.5h15"/></g></svg>
    </span>
  </div>

  <ul class="contact-list">
    <li>+91 97415 60382</li>
    <li>kelvanjoshi@mailbrook.example</li>
    <li>www.greymarshcontracts.example</li>
  </ul>

  <p class="company"><span class="line-1">GREYMARSH ENGINEERING</span><span class="line-2">CONTRACTS LLP</span></p>

  <address class="address">
    Block No.317, Wing C, Tulvo Trade Court,<br>
    Manek Pural Road, Ruparel Industrial Estate,<br>
    Goregaon(E), Mumbai - 400 063
  </address>
</section>

</body>
</html>
```